Law Offices business card

Hi there, I'll need business card for the Law Offices of Colin Matheny. The information must convey his strategic approach and quick resolution to complex business litigation needs. Please emphasize Civil Litigation, Corporate Law, Business Governance and Real Estate Law. Colin has over 25 years of experience in these fields.The card should be modern and edgy and the message should be clear. Please consult his current website for ideas.

```html
<!DOCTYPE html>
<html lang="en">
<head>
<meta charset="utf-8">
<title>Law Offices of Colin Matheny – Business Card</title>
<link rel="stylesheet" href="https://fonts.googleapis.com/css2?family=Arimo:wght@400;700&display=swap">
<style>
  :root{
    --stage:#3a3b3d;
    --brand-red:#bf4b4c;
    --brand-red-deep:#a93d3e;
    --ink:#0b0b0c;
    --ink-soft:#1c1c1e;
    --paper:#ffffff;
    --muted:#e6e6e6;
  }
  *{box-sizing:border-box;margin:0;padding:0}
  html,body{width:1200px;height:950px;overflow:hidden}
  body{background:var(--stage);font-family:"Arimo",Arial,sans-serif;position:relative}

  .card{position:absolute;width:600px;height:343px;overflow:hidden;box-shadow:0 18px 40px rgba(0,0,0,.45)}
  .card--front{left:70px;top:110px;background:linear-gradient(160deg,var(--brand-red) 0%,var(--brand-red-deep) 100%)}
  .card--back{left:530px;top:497px;background:linear-gradient(150deg,var(--ink-soft) 0%,var(--ink) 60%)}

  /* firm name block: square mark sits at the left edge of the name */
  .firm-name{position:absolute;color:var(--paper);font-weight:700;line-height:1;display:flex;align-items:flex-start;gap:10px}
  .firm-name__mark{width:14px;height:14px;background:var(--paper);margin-top:26px;flex:none}
  .firm-name__pre{display:block;font-size:11px;letter-spacing:1.5px;text-transform:uppercase;margin-bottom:6px}
  .firm-name__main{display:block;font-size:32px;letter-spacing:-.5px}
  .firm-name__suffix{font-size:19px}

  .card--front .firm-name{left:190px;top:86px}
  .front-underline{position:absolute;left:214px;top:186px;width:226px;height:1px;background:linear-gradient(90deg,rgba(255,255,255,0),var(--paper) 30%,var(--paper) 70%,rgba(255,255,255,0))}

  .front-footer{position:absolute;left:0;right:0;top:250px;display:flex;align-items:center;justify-content:center;gap:12px}
  .front-footer__rule{width:50px;height:1px;background:var(--paper);opacity:.85}
  .front-footer__site{color:var(--paper);font-size:12px;letter-spacing:3px}

  .card--back .firm-name{left:48px;top:128px}
  .card--back .firm-name__mark{background:var(--brand-red)}
  .card--back .firm-name__main{font-size:30px}

  .divider{position:absolute;left:312px;top:20px;width:1px;height:235px;background:linear-gradient(180deg,rgba(255,255,255,0),rgba(255,255,255,.55),rgba(255,255,255,0))}

  .contact{position:absolute;left:336px;top:30px;color:var(--muted);font-size:14px;line-height:1.35}
  .contact__name{color:var(--brand-red);font-size:19px;font-weight:700;line-height:1.1}
  .contact__title{margin-bottom:8px}
  .contact__address{margin-bottom:4px}
  .contact__list{list-style:none}
  .contact__item{display:flex;align-items:center;gap:8px;height:21px}
  .contact__item svg{width:14px;height:14px;fill:var(--brand-red);flex:none}

  .back-band{position:absolute;left:0;right:0;bottom:0;height:54px;background:var(--brand-red);border-top:5px solid var(--paper)}
  .back-band__line{position:absolute;left:0;width:260px;bottom:9px;height:2px;background:var(--paper)}
</style>
</head>
<body>

<section class="card card--front" aria-label="Card front">
  <div class="firm-name">
    <span class="firm-name__mark"></span>
    <div>
      <span class="firm-name__pre">Law Offices of</span>
      <span class="firm-name__main">Colin<br>Matheny<span class="firm-name__suffix">, PA</span></span>
    </div>
  </div>
  <span class="front-underline"></span>
  <div class="front-footer">
    <span class="front-footer__rule"></span>
    <span class="front-footer__site">www.mathenylaw.com</span>
    <span class="front-footer__rule"></span>
  </div>
</section>

<section class="card card--back" aria-label="Card back">
  <div class="firm-name">
    <span class="firm-name__mark"></span>
    <div>
      <span class="firm-name__pre">Law Offices of</span>
      <span class="firm-name__main">Colin<br>Matheny<span class="firm-name__suffix">, PA</span></span>
    </div>
  </div>

  <span class="divider"></span>

  <div class="contact">
    <p class="contact__name">Colin Matheny</p>
    <p class="contact__title">President</p>
    <p class="contact__address">4127 Harrow Lane<br>Glen Cove, NY 11542</p>
    <ul class="contact__list">
      <li class="contact__item">
        <svg viewBox="0 0 16 16" aria-hidden="true"><path d="M3 1h3l1 4-2 1c1 2 3 4 5 5l1-2 4 1v3c0 1-1 2-2 2C7 15 1 9 1 3c0-1 1-2 2-2z"/></svg>
        <span>516 820 4471</span>
      </li>
      <li class="contact__item">
        <svg viewBox="0 0 16 16" aria-hidden="true"><path d="M4 0h8a1 1 0 0 1 1 1v14a1 1 0 0 1-1 1H4a1 1 0 0 1-1-1V1a1 1 0 0 1 1-1zm1 2v10h6V2zm3 11a1 1 0 1 0 0 2 1 1 0 0 0 0-2z"/></svg>
        <span>516 902 3318</span>
      </li>
      <li class="contact__item">
        <svg viewBox="0 0 16 16" aria-hidden="true"><path d="M4 1h7l2 2v3H4zM1 7h14v6h-2v2H3v-2H1zm4 4v3h6v-3z"/></svg>
        <span>516 744 2690</span>
      </li>
      <li class="contact__item">
        <svg viewBox="0 0 16 16" aria-hidden="true"><path d="M1 3h14v1L8 9 1 4zm0 2.5 7 5 7-5V13H1z"/></svg>
        <span>colin@mathenylaw.com</span>
      </li>
      <li class="contact__item">
        <svg viewBox="0 0 16 16" aria-hidden="true"><path d="M8 1a7 7 0 1 0 0 14A7 7 0 0 0 8 1zm0 2c.8 1 1.3 2.4 1.4 4H6.6C6.7 5.4 7.2 4 8 3zM3.1 9h2.4c.1 1.4.5 2.7 1.1 3.7A5 5 0 0 1 3.1 9zm0-2a5 5 0 0 1 3.5-3.7C6 4.3 5.6 5.6 5.5 7zm4.9 6c-.8-1-1.3-2.4-1.4-4h2.8c-.1 1.6-.6 3-1.4 4zm1.4-.3c.6-1 1-2.3 1.1-3.7h2.4a5 5 0 0 1-3.5 3.7zM10.5 7c-.1-1.4-.5-2.7-1.1-3.7A5 5 0 0 1 12.9 7z"/></svg>
        <span>www.mathenylaw.com</span>
      </li>
    </ul>
  </div>

  <div class="back-band"><span class="back-band__line"></span></div>
</section>

</body>
</html>
```